Woman owned consulting company needs an elegant and modern business card design

I need a business card design for my new consulting company, Mara Quillon Consulting. I am looking for something that is simple and elegant, but also creative and original. You can use either version of the logo that are attached. I have also included the information that needs to be featured on the business card.

Contact Information for Business Card

Requirements
Must have
• The logo and the font type and a standard business card size. Use shades of gray/silver and or rose gold that are in the logo.
• I didn't realize that my actual logo wasn't attached. Please incorporate in the designs.
Should not have
• Colors that are different from my logo

```html
<!DOCTYPE html>
<html lang="en">
<head>
<meta charset="utf-8">
<title>Mara Quillon Consulting – Business Cards</title>
<link rel="stylesheet" href="https://fonts.googleapis.com/css2?family=Cinzel:wght@400;600&family=Crimson+Text:wght@400&display=swap">
<style>
  :root {
    --backdrop: #c6c6c6;
    --card: #f3f3f3;
    --ink-dark: #34383a;
    --ink-mid: #4a4a4a;
    --silver: #9a9a9a;
    --silver-light: #c9c9c9;
    --band: #3b3f41;
    --band-text: #f1f1f1;
  }
  * { box-sizing: border-box; margin: 0; padding: 0; }
  html, body {
    width: 1200px; height: 852px; overflow: hidden;
    background: var(--backdrop);
  }
  .stage {
    position: relative; width: 1200px; height: 852px;
    display: flex; align-items: center; justify-content: center; gap: 40px;
  }
  .card {
    position: relative; width: 540px; height: 309px;
    background: var(--card); border-radius: 14px; overflow: hidden;
    box-shadow: 0 6px 18px rgba(0,0,0,0.18);
  }

  /* Brand name stand-in: plain text in the body font, one colour, one weight */
  .brand {
    display: flex; align-items: center;
    font-family: "Crimson Text", serif; font-weight: 400; color: var(--silver);
  }
  .brand-dot { border-radius: 50%; background: var(--silver); flex: none; }
  .brand-name { line-height: 1.15; }

  /* Back side */
  .card-back .brand {
    position: absolute; left: 0; right: 0; top: 104px;
    justify-content: center; gap: 16px;
  }
  .card-back .brand-dot { width: 38px; height: 38px; }
  .card-back .brand-name { font-size: 28px; }
  .card-back .website {
    position: absolute; left: 0; right: 0; top: 205px; text-align: center;
    font-family: "Crimson Text", serif; font-size: 14px; color: var(--ink-mid); letter-spacing: 0.4px;
  }

  /* Front side */
  .card-front .brand {
    position: absolute; left: 30px; top: 112px; width: 240px; gap: 14px;
  }
  .card-front .brand-dot { width: 52px; height: 52px; }
  .card-front .brand-name { font-size: 26px; }
  .card-front .details { position: absolute; left: 286px; top: 66px; }
  .holder-name {
    font-family: "Cinzel", serif; font-weight: 600; font-size: 20px;
    color: var(--ink-dark); letter-spacing: 1px;
  }
  .holder-role {
    font-family: "Crimson Text", serif; font-size: 13px; color: var(--ink-mid); margin-bottom: 14px;
  }
  .contact-list { list-style: none; }
  .contact-list li {
    display: flex; align-items: center; gap: 8px; height: 19px;
    font-family: "Crimson Text", serif; font-size: 13.5px; color: var(--ink-dark);
  }
  .contact-list svg { width: 12px; height: 12px; fill: var(--ink-dark); flex: none; }
  .base-strip {
    position: absolute; left: 0; right: 0; bottom: 0; height: 16px; background: var(--silver-light);
  }
  .name-band {
    position: absolute; right: 0; bottom: 0; width: 262px; height: 48px;
    background: var(--band); border-top-left-radius: 18px;
    display: flex; align-items: center; justify-content: center;
    font-family: "Cinzel", serif; font-size: 13.5px; color: var(--band-text); letter-spacing: 0.6px;
  }
</style>
</head>
<body>
<main class="stage">

  <section class="card card-back" aria-label="Card back">
    <div class="brand">
      <span class="brand-dot"></span>
      <span class="brand-name">Mara Quillon<br>Consulting, LLC</span>
    </div>
    <p class="website">www.maraquillonconsulting.com</p>
  </section>

  <section class="card card-front" aria-label="Card front">
    <div class="brand">
      <span class="brand-dot"></span>
      <span class="brand-name">Mara Quillon<br>Consulting</span>
    </div>
    <div class="details">
      <h1 class="holder-name">Mara Quillon</h1>
      <p class="holder-role">Owner</p>
      <ul class="contact-list">
        <li>
          <svg viewBox="0 0 24 24" aria-hidden="true"><path d="M6.6 10.8a15.1 15.1 0 0 0 6.6 6.6l2.2-2.2a1 1 0 0 1 1-.25 11.4 11.4 0 0 0 3.6.57 1 1 0 0 1 1 1V20a1 1 0 0 1-1 1A17 17 0 0 1 3 4a1 1 0 0 1 1-1h3.5a1 1 0 0 1 1 1c0 1.25.2 2.450.57 3.57a1 1 0 0 1-.25 1z"/></svg>
          555-014-2271
        </li>
        <li>
          <svg viewBox="0 0 24 24" aria-hidden="true"><path d="M2 5h20v14H2z M4 7v.5l8 5 8-5V7l-8 5z" fill-rule="evenodd"/></svg>
          mara@maraquillonconsulting.com
        </li>
        <li>
          <svg viewBox="0 0 24 24" aria-hidden="true"><circle cx="12" cy="12" r="10"/><path d="M2 12h20M12 2c3 3 3 17 0 20M12 2c-3 3-3 17 0 20" stroke="#f3f3f3" stroke-width="1.5" fill="none"/></svg>
          www.maraquillonconsulting.com
        </li>
      </ul>
    </div>
    <div class="base-strip"></div>
    <div class="name-band">Mara Quillon Consulting, LLC</div>
  </section>

</main>
</body>
</html>
```